Business Card for a Dental Office

The design should communicate integrity, quality and reliability. We also want the card look elegant, simple, but still stand out, different from the traditional-dental-office business card.

Industry/Entity Type

Business

```html
<!DOCTYPE html>
<html lang="en">
<head>
<meta charset="utf-8">
<title>Harbor Dental Studio – Business Card</title>
<link href="https://fonts.googleapis.com/css2?family=Oswald:wght@500;600&family=Open+Sans:wght@400;600&display=swap" rel="stylesheet">
<style>
  :root {
    --stage: #3a3331;
    --card: #141414;
    --card-edge: #222;
    --white: #f2f2f2;
    --muted: #cfcfcf;
    --gold: #d9b52a;
    --divider: #8a8a8a;
  }
  * { box-sizing: border-box; margin: 0; padding: 0; }
  html, body {
    width: 1200px; height: 814px; overflow: hidden;
    background: var(--stage);
  }
  .stage {
    position: relative; width: 1200px; height: 814px;
    display: flex; align-items: center; justify-content: center; gap: 40px;
  }
  .card {
    position: relative;
    width: 520px; height: 297px;
    background: var(--card);
    border: 1px solid var(--card-edge);
    border-radius: 4px;
    box-shadow: 0 10px 28px rgba(0,0,0,.45);
    color: var(--white);
    font-family: "Open Sans", sans-serif;
  }
  /* back side */
  .card--back {
    display: flex; flex-direction: column; align-items: center; justify-content: center;
  }
  .brand-mark {
    display: flex; align-items: center; gap: 12px;
  }
  .brand-mark__square {
    width: 26px; height: 26px; background: var(--gold);
  }
  .brand-mark__name {
    font-family: "Oswald", sans-serif; font-weight: 600;
    font-size: 30px; letter-spacing: 1px; text-transform: uppercase;
    color: var(--white);
  }
  .card--back .web {
    margin-top: 26px; font-size: 13px; letter-spacing: 3px; color: var(--muted);
  }
  /* front side */
  .front-brand {
    position: absolute; top: 52px; left: 0; right: 0;
    text-align: center;
  }
  .front-brand .brand-mark { justify-content: center; }
  .front-brand .brand-mark__square { width: 20px; height: 20px; }
  .front-brand .brand-mark__name { font-size: 28px; }
  .tagline {
    margin-top: 2px;
    font-family: "Oswald", sans-serif; font-weight: 500;
    font-size: 12.5px; letter-spacing: 1.2px; text-transform: uppercase;
    color: var(--gold);
  }
  .details {
    position: absolute; top: 140px; left: 40px; right: 30px;
    display: flex; align-items: stretch;
  }
  .person {
    width: 210px; text-align: right; padding-right: 18px;
    font-size: 13px; line-height: 1.45; color: var(--white);
  }
  .person__name { font-size: 17px; font-weight: 600; color: var(--gold); }
  .divider { width: 1px; background: var(--divider); }
  .contacts {
    list-style: none; padding-left: 18px;
    font-size: 13.5px; line-height: 1.55;
  }
  .contacts li { display: flex; align-items: center; gap: 9px; white-space: nowrap; }
  .contacts svg { width: 13px; height: 13px; fill: var(--gold); flex: none; }
</style>
</head>
<body>
<main class="stage">
  <section class="card card--back" aria-label="Card back">
    <div class="brand-mark">
      <span class="brand-mark__square"></span>
      <span class="brand-mark__name">Harbor Dental Studio</span>
    </div>
    <p class="web">www.harbordental.com</p>
  </section>

  <section class="card card--front" aria-label="Card front">
    <header class="front-brand">
      <div class="brand-mark">
        <span class="brand-mark__square"></span>
        <span class="brand-mark__name">Harbor Dental Studio</span>
      </div>
      <p class="tagline">Gentle care for every smile we meet</p>
    </header>

    <div class="details">
      <div class="person">
        <p class="person__name">Daniel Reyes</p>
        <p>CEO/Founder</p>
        <p>2140 Cedar Ridge Road</p>
        <p>Juneau, Alaska 99801</p>
      </div>
      <span class="divider"></span>
      <ul class="contacts">
        <li><svg viewBox="0 0 16 16"><path d="M3.5 1l3 3-1.8 2a9 9 0 0 0 5.3 5.3l2-1.8 3 3-2 2.5C7 14.5 1.5 9 1 3.5z"/></svg>907 555 0142</li>
        <li><svg viewBox="0 0 16 16"><path d="M4 0h8a1 1 0 0 1 1 1v14a1 1 0 0 1-1 1H4a1 1 0 0 1-1-1V1a1 1 0 0 1 1-1zm1 2v10h6V2zm3 11a1 1 0 1 0 0 2 1 1 0 0 0 0-2z"/></svg>907 555 0187</li>
        <li><svg viewBox="0 0 16 16"><path d="M4 1h7l2 2v3H4zM1 7h14v7H1zm3 2v1h2V9zm4 0v1h2V9zm-4 2v1h2v-1zm4 0v1h2v-1z"/></svg>907 555 0163</li>
        <li><svg viewBox="0 0 16 16"><path d="M1 3h14v10H1zm1.5 1.2L8 8.5l5.5-4.3z"/></svg>hello@harbordental.com</li>
        <li><svg viewBox="0 0 16 16"><circle cx="8" cy="8" r="7"/></svg>www.harbordental.com</li>
      </ul>
    </div>
  </section>
</main>
</body>
</html>
```